Marlow Estate Fixers (Handyman / Home Improvement Company)

Looking for a double sided professional looking business card with Logo attached to be highlighted on one side and throwing in an image of a handyman as an option would be nice to see as well. We are a company focused on providing quality Handyman and Home improvement services in a timely manner that is done right the first time with integrity

Industry/Entity Type

Handyman / Home Improvement

Contact Information for Business Card

(LOGO, Name, Mobile and office phone numbers, email) on front side of card, (the words "The SOLUTION to all of your Handyman and Home Improvement needs" followed by "Family Owned and Operated" at the very bottom) on the back.

Colors
EB3D1F
EC4F4E
F09395
F8D3D4
FCEDEE

Requirements
Must have
• Red, Gray, Black Color scheme
Should not have
• No Yellow or Blue colors

```html
<!DOCTYPE html>
<html lang="en">
<head>
<meta charset="utf-8">
<title>Marlow Estate Fixers – Business Card</title>
<link href="https://fonts.googleapis.com/css2?family=Montserrat:wght@400;600;700;800&family=Oswald:wght@700&display=swap" rel="stylesheet">
<style>
  :root{
    --red:#EB2D2F;
    --red-deep:#E0262A;
    --ink:#1c1c1c;
    --charcoal:#333335;
    --paper:#ffffff;
    --stage:#1e1e1e;
    --figure-blue:#8a5a3a;
    --figure-brown:#9c6a42;
  }
  *{box-sizing:border-box;margin:0;padding:0}
  html,body{width:1200px;height:1059px;overflow:hidden}
  body{background:var(--stage);position:relative;font-family:"Montserrat",sans-serif}

  .card{position:absolute;overflow:hidden;border-radius:26px}

  /* Front */
  .card-front{left:250px;top:95px;width:701px;height:401px;background:var(--paper)}
  .brand{position:absolute;left:96px;top:128px;width:211px;height:144px;display:flex;align-items:center;justify-content:center;gap:8px}
  .brand-dot{width:14px;height:14px;border-radius:50%;background:var(--red);flex:none}
  .brand-name{font-weight:800;font-size:24px;line-height:1.1;color:var(--red);text-transform:uppercase;text-align:left}
  .divider{position:absolute;left:345px;top:116px;width:2px;height:168px;background:var(--red)}
  .person{position:absolute;left:375px;top:116px}
  .person-name{font-weight:700;font-size:28px;color:var(--red);line-height:1.2}
  .person-role{font-weight:400;font-size:18px;color:var(--ink);margin-top:2px}
  .contacts{position:absolute;left:375px;top:192px;list-style:none}
  .contacts li{display:flex;align-items:center;height:31px;font-size:19px;color:var(--ink)}
  .contacts svg{width:20px;height:20px;margin-right:14px;flex:none}
  .band{position:absolute;bottom:0;height:12px}
  .band-red{left:0;width:354px;background:var(--red);clip-path:polygon(0 0,100% 0,97% 100%,0 100%)}
  .band-dark{right:0;left:352px;background:var(--charcoal);clip-path:polygon(2% 0,100% 0,100% 100%,0 100%)}

  /* Back */
  .card-back{left:251px;top:529px;width:735px;height:420px;background:var(--red)}
  .tagline{position:absolute;left:0;right:0;top:26px;text-align:center;font-family:"Oswald",sans-serif;font-weight:700;color:var(--paper);font-size:35px;line-height:44px;letter-spacing:-0.3px}
  .handyman{position:absolute;left:146px;top:118px;width:115px;height:285px;border-radius:40px 40px 8px 8px;background:linear-gradient(180deg,#3f6fb0 0%,#3f6fb0 45%,var(--figure-brown) 55%,var(--figure-brown) 100%)}
  .brand-back{position:absolute;left:375px;top:144px;width:284px;height:197px;display:flex;align-items:center;justify-content:center;gap:10px}
  .brand-back .brand-dot{background:var(--paper);width:16px;height:16px}
  .brand-back .brand-name{color:var(--paper);font-size:30px}
  .family{position:absolute;left:300px;width:432px;top:368px;text-align:center;font-weight:700;font-size:24px;color:var(--paper)}
</style>
</head>
<body>
  <section class="card card-front" aria-label="Business card front">
    <div class="brand">
      <span class="brand-dot"></span>
      <span class="brand-name">Marlow Estate Fixers</span>
    </div>
    <div class="divider"></div>
    <div class="person">
      <p class="person-name">Daniel Hartley</p>
      <p class="person-role">Owner</p>
    </div>
    <ul class="contacts">
      <li>
        <svg viewBox="0 0 20 20" aria-hidden="true"><rect x="5" y="1.5" width="10" height="17" rx="2" fill="none" stroke="#EB2D2F" stroke-width="2"/><circle cx="10" cy="15" r="1.2" fill="#EB2D2F"/></svg>
        044-555 010 234
      </li>
      <li>
        <svg viewBox="0 0 20 20" aria-hidden="true"><path d="M2 7c0-3 3-4 8-4s8 1 8 4v1h-4V6H6v2H2z" fill="#EB2D2F"/><path d="M5 9h10l2 8H3z" fill="#EB2D2F"/><circle cx="10" cy="13" r="2" fill="#fff"/></svg>
        044-555 010 235
      </li>
      <li>
        <svg viewBox="0 0 20 20" aria-hidden="true"><rect x="1.5" y="4" width="17" height="12" fill="#EB2D2F"/><path d="M1.5 4l8.5 7 8.5-7" fill="none" stroke="#fff" stroke-width="1.6"/></svg>
        info@marlowfixers.com
      </li>
    </ul>
    <div class="band band-red"></div>
    <div class="band band-dark"></div>
  </section>

  <section class="card card-back" aria-label="Business card back">
    <p class="tagline">Your SOLUTION to all of<br>your Handyman and Home Improvement Needs</p>
    <div class="handyman" role="img" aria-label="Illustration of a handyman in a hard hat holding a wrench, wearing a tool belt"></div>
    <div class="brand brand-back">
      <span class="brand-dot"></span>
      <span class="brand-name">Marlow Estate Fixers</span>
    </div>
    <p class="family">Family Owned and Operated</p>
  </section>
</body>
</html>
```